Social Media App Needs PPT Template

We need a PowerPoint template for a new social media company based in the DC area called "Bold Ledger." We provide an interactive digital platform for executives to share actionable advice. We would like to see designs that use our orange logo color as an accent, but are mainly grey, white, and black. The final design should communicate clean, chic, modern, and professional.

Target Market(s)

Executives

Industry/Entity Type

Information Technology

Font styles to use
Sans Serif

Colors
f78f20
fbe7d2
ffffff
000000
e8e8e8
757575

Requirements
Must have
• My project must have title page and many options for the body of the ppt (graphs, tables, etc). It also needs to be easy to modify. I must have someone who is experienced in creating powerpoint templates.
Nice to have
• It would be nice to have a very modern and clean design that includes the logo on every page, but still leaves a lot of room for the content of the slide
Should not have
• My design project should not look to busy.

```html
<!DOCTYPE html>
<html lang="en">
<head>
<meta charset="utf-8">
<title>Bold Ledger – Table Slide</title>
<link rel="stylesheet" href="https://fonts.googleapis.com/css2?family=Oswald:wght@500&family=Lato:wght@300;400&display=swap">
<style>
  :root {
    --backdrop: #555555;
    --paper: #ffffff;
    --accent: #f4921f;
    --navy: #222d3c;
    --ink: #4a4a4a;
    --muted: #757575;
    --rule: #8a8a8a;
  }
  * { margin: 0; padding: 0; box-sizing: border-box; }
  html, body {
    width: 1200px; height: 960px; overflow: hidden;
    background: var(--backdrop);
  }
  .slide {
    position: absolute; left: 0; top: 30px;
    width: 1200px; height: 900px;
    background: var(--paper);
    font-family: "Lato", sans-serif;
  }
  .accent-stripe {
    position: absolute; left: 0; top: 18px; width: 100%; height: 14px;
    background: var(--accent);
  }
  .header-band {
    position: absolute; left: 0; top: 35px; width: 100%; height: 116px;
    background: var(--navy);
  }
  .slide-title {
    position: absolute; left: 51px; top: 58px;
    font-family: "Oswald", sans-serif; font-weight: 500;
    font-size: 56px; line-height: 1; letter-spacing: -1px;
    color: var(--paper); text-transform: uppercase;
  }
  .brand {
    position: absolute; right: 46px; top: 74px;
    display: flex; align-items: center; gap: 12px;
    font-family: "Oswald", sans-serif; font-weight: 500;
    font-size: 32px; line-height: 1; letter-spacing: 3px;
    color: var(--paper); text-transform: uppercase;
  }
  .brand-dot {
    width: 34px; height: 34px; border-radius: 50%;
    background: var(--accent);
  }
  .table-rule {
    position: absolute; left: 61px; top: 284px; width: 1090px; height: 2px;
    background: var(--rule);
  }
  .data-table {
    position: absolute; left: 60px; top: 310px; width: 1091px;
    border-collapse: collapse;
  }
  .data-table th {
    height: 68px; vertical-align: middle;
    font-weight: 400; font-size: 18px; color: var(--muted);
    text-align: center;
  }
  .data-table td {
    height: 94px; vertical-align: middle; text-align: center;
    font-weight: 300; font-size: 35px; color: var(--ink);
  }
  .data-table .row-label {
    text-align: left; padding-left: 116px; width: 388px;
    font-size: 21px; font-weight: 400;
  }
  .data-table .value-col { width: 234px; }
  .data-table tr.is-highlight td {
    background: var(--accent); color: var(--paper);
  }
  .footer-rule {
    position: absolute; left: 807px; top: 831px; width: 352px; height: 1.5px;
    background: var(--ink);
  }
  .footer-note {
    position: absolute; right: 43px; top: 855px;
    font-size: 16px; font-weight: 400; color: var(--muted);
  }
</style>
</head>
<body>
  <main class="slide">
    <div class="accent-stripe"></div>
    <header class="header-band">
      <h1 class="slide-title" style="top:23px">Title Goes Here</h1>
    </header>
    <div class="brand"><span class="brand-dot"></span>Bold Ledger</div>

    <div class="table-rule"></div>
    <table class="data-table">
      <thead>
        <tr>
          <th></th>
          <th class="value-col">A</th>
          <th class="value-col">B</th>
          <th class="value-col">C</th>
        </tr>
      </thead>
      <tbody>
        <tr class="is-highlight">
          <td class="row-label">Type 1</td><td>20</td><td>30</td><td>40</td>
        </tr>
        <tr>
          <td class="row-label">Type 2</td><td>50</td><td>60</td><td>70</td>
        </tr>
        <tr class="is-highlight">
          <td class="row-label">Type 3</td><td>80</td><td>90</td><td>100</td>
        </tr>
      </tbody>
    </table>

    <div class="footer-rule"></div>
    <p class="footer-note">www.boldledger.com &nbsp;|&nbsp; Page 7</p>
  </main>
</body>
</html>
```